Need help in designing new business card utilizing our new logo.

BuildMark Solutions works with Construction Business Owners, Managers & IT Professionals to strengthen software usage and increase user productivity.

Our Construction Accounting and Mobile Field Management Software Clients engage with us in the following areas:

New Software Implementations
Software Re-Implementations
Redesigning Software Usage at the User Level
Project Coordination & Management
Continued Software Support

Old tag line:
Weighing Options - Implementing Solutions

www.buildmark-solutions.example

Ridge 4 is a product, but not needed for a new business card.

```html
<!DOCTYPE html>
<html lang="en">
<head>
<meta charset="utf-8">
<title>BuildMark Solutions – Business Card</title>
<link rel="stylesheet" href="https://fonts.googleapis.com/css2?family=Open+Sans:wght@400;600;700&display=swap">
<style>
  :root {
    --backdrop: #3b3b3d;
    --paper: #f3f3f3;
    --brand-blue: #0c14a0;
    --back-blue: #1119aa;
    --ink-grey: #4a4a4a;
    --white: #ffffff;
  }
  * { margin: 0; padding: 0; box-sizing: border-box; }
  html, body { width: 1200px; height: 960px; overflow: hidden; }
  body {
    background: var(--backdrop);
    font-family: "Open Sans", Arial, sans-serif;
    position: relative;
  }
  .card { position: absolute; width: 600px; height: 342px; overflow: hidden; }
  .card-front { left: 322px; top: 110px; background: var(--paper); }
  .card-back { left: 320px; top: 493px; background: var(--back-blue); color: var(--white); }

  .brand { position: absolute; display: flex; align-items: center; gap: 12px; }
  .card-front .brand { left: 32px; top: 44px; }
  .brand-square { width: 44px; height: 44px; background: var(--brand-blue); flex: none; }
  .brand-name {
    font-size: 20px; font-weight: 600; line-height: 22px;
    color: var(--brand-blue); letter-spacing: 0.5px;
  }

  .name-banner { position: absolute; left: 355px; top: 56px; width: 218px; height: 53px; }
  .name-banner svg { position: absolute; inset: 0; }
  .person-name, .person-role {
    position: absolute; right: 10px; color: var(--white); font-weight: 700; text-align: right;
    white-space: nowrap;
  }
  .person-name { top: 5px; font-size: 18px; letter-spacing: 0.3px; }
  .person-role { top: 29px; font-size: 14px; }

  .address { position: absolute; right: 36px; top: 154px; text-align: right; font-size: 15px; line-height: 20px; color: var(--ink-grey); }
  .contacts { position: absolute; right: 36px; top: 200px; list-style: none; font-size: 15px; color: var(--ink-grey); }
  .contacts li { display: flex; justify-content: flex-end; align-items: center; gap: 7px; height: 19.5px; white-space: nowrap; }
  .contacts svg { width: 14px; height: 14px; fill: var(--brand-blue); flex: none; }

  .service-band {
    position: absolute; left: 0; right: 0; top: 293px; height: 30px; background: var(--brand-blue);
    color: var(--white); font-size: 14px; text-align: right; padding-right: 35px; line-height: 30px;
  }

  .card-back .brand {
    left: 50px; top: 88px; width: 160px;
    flex-direction: column; align-items: center; gap: 12px;
  }
  .card-back .brand-square { width: 100px; height: 100px; background: var(--white); }
  .card-back .brand-name { color: var(--white); font-size: 18px; line-height: 22px; text-align: center; }

  .engagement { position: absolute; left: 235px; top: 77px; }
  .engagement-intro { font-size: 15px; font-weight: 700; line-height: 19px; text-transform: uppercase; }
  .engagement-list { list-style: none; font-size: 15px; line-height: 19px; }
  .engagement-list li::before { content: "• "; }
  .tagline { position: absolute; left: 0; width: 556px; top: 296px; text-align: center; font-size: 15px; }
</style>
</head>
<body>
  <section class="card card-front" aria-label="Business card front">
    <div class="brand">
      <span class="brand-square"></span>
      <span class="brand-name">BUILDMARK<br>SOLUTIONS</span>
    </div>

    <div class="name-banner">
      <svg viewBox="0 0 218 53" width="218" height="53" aria-hidden="true">
        <polygon points="39,0 218,0 218,53 0,53" fill="var(--brand-blue)"/>
      </svg>
      <span class="person-name">DANA R.WHITLEY</span>
      <span class="person-role">OWNER</span>
    </div>

    <p class="address">14b harbor street-PMB118<br>lakeview falls NY 12000</p>

    <ul class="contacts">
      <li>800-555-0142ext.100
        <svg viewBox="0 0 16 16" aria-hidden="true"><path d="M1 5c0-2 3-3 7-3s7 1 7 3v1h-4V5H5v1H1z M4 7h8l2 7H2z"/></svg></li>
      <li>518-555-0199
        <svg viewBox="0 0 16 16" aria-hidden="true"><path d="M4 0h8v16H4z M5.5 2v10h5V2z" fill-rule="evenodd"/></svg></li>
      <li>dana.whitley@buildmark-solutions.example
        <svg viewBox="0 0 16 16" aria-hidden="true"><path d="M1 3h14v2L8 9 1 5z M1 7l7 4 7-4v6H1z"/></svg></li>
      <li>www.buildmark-solutions.example
        <svg viewBox="0 0 16 16" aria-hidden="true"><circle cx="8" cy="8" r="7"/></svg></li>
    </ul>

    <div class="service-band">CONSTRUCTION ACCOUNTING SOFTWARE CONSULTANTS</div>
  </section>

  <section class="card card-back" aria-label="Business card back">
    <div class="brand">
      <span class="brand-square"></span>
      <span class="brand-name">BUILDMARK<br>SOLUTIONS</span>
    </div>

    <div class="engagement">
      <p class="engagement-intro">Our construction accounting<br>and mobile field management<br>software clients engage with us<br>in the following areas:</p>
      <ul class="engagement-list">
        <li>New Software Implementations</li>
        <li>Software Re-Implementations</li>
        <li>Redesigning Software Usage at the User Level</li>
        <li>Project Coordination &amp; Management</li>
        <li>Continued Software Support</li>
      </ul>
    </div>

    <p class="tagline">WEIGHING OPTIONS - IMPLEMENTING SOLUTIONS</p>
  </section>
</body>
</html>
```